Hybrid Seed corn and Soybean Sales business needs a website.

We here at "KW Grain" feel that we need a website to show a very professional side to our customer base. Although no actual ordering will take place on this website, we would like to put Plot and field trail data on the website. Along with a brief page for each of our hybrids and a place for customers to sign up for a newsletter. The company we sell hybrids for is MolvanGrain.com... Im not sure how this process works as far as myself updating the information or having the data actually put on the website, but feel free to contact me if you need the information. I will attach the logo for the company, (KW Grain).

Target Market(s)

Farmers, "Producers", Corn and soybean production

Industry/Entity Type

Business

Coding

Coded - Design and coding required

Number of Pages Required

5+ page

Colors
f78f20
ffffff

Requirements
Nice to have
• Similar layout to http://www.molvangrain.com/
• And it would be nice to incorporate our story into the website
• http://www.molvangrain.com/our-story/molvan-today/

```html
<!DOCTYPE html>
<html lang="en">
<head>
<meta charset="utf-8">
<title>KW Grain — Hybrid Seed Corn &amp; Soybeans</title>
<link rel="stylesheet" href="https://fonts.googleapis.com/css2?family=Source+Sans+3:wght@300;400;600;700&display=swap">
<style>
:root{
  --orange:#f78f20;
  --green:#5f9a1e;
  --green-light:#86b52c;
  --grey-band:#e5e2e2;
  --dark:#3b3a3a;
  --text:#555;
  --heading:#666;
  --white:#fff;
}
*{box-sizing:border-box;margin:0;padding:0}
html,body{width:811px;height:1200px;overflow:hidden}
body{position:relative;font-family:"Source Sans 3",Arial,sans-serif;color:var(--text);background:var(--white)}
a{color:inherit;text-decoration:none}
.abs{position:absolute}

.topbar{left:0;top:0;width:811px;height:24px;background:linear-gradient(#8cba34,#6e9f22);color:var(--white);font-size:10px}
.topbar .links{left:74px;top:6px;display:flex;gap:21px}
.topbar .call{right:70px;top:5px;font-size:8.5px}
.topbar .call b{font-size:11px;font-weight:400}
.topbar .agent{right:56px;top:4px;width:10px;height:16px;border-radius:5px 5px 2px 2px;background:#2c2c2c}

.header{left:0;top:24px;width:811px;height:71px;background:var(--white)}
.brand{left:74px;top:30px;display:flex;align-items:center;gap:6px}
.brand .dot{width:26px;height:26px;border-radius:50%;background:var(--green-light)}
.brand span{font-size:22px;font-weight:700;color:var(--orange);letter-spacing:.5px}
.search{left:705px;top:34px;width:26px;height:24px;background:var(--orange)}
.nav{left:223px;top:73px;display:flex;font-size:10px;color:#333}
.nav a{padding:2px 9.5px 8px}
.nav a.active{color:var(--orange);border-bottom:2px solid var(--orange)}

.hero{left:0;top:95px;width:811px;height:261px;background:radial-gradient(ellipse at 50% 20%,#d9c04a 0%,#8fb83a 25%,#4e8a1c 60%,#2f5e12 100%)}
.arrow{width:29px;height:28px;background:var(--orange)}
.quote{left:132px;top:190px;width:552px;height:71px;background:rgba(40,50,20,.45);color:var(--white);font-size:13.5px;font-weight:300;line-height:14px;text-align:center;padding-top:22px}

.video{left:66px;top:378px;width:186px;height:105px;background:linear-gradient(180deg,#3b2a1c 0%,#8a4a1a 55%,#f0a030 75%,#2a1a10 100%)}
.welcome-h{left:265px;top:372px;font-size:22px;font-weight:400;color:var(--heading)}
.welcome-h em{font-style:normal;color:var(--orange)}
.welcome-p{left:267px;top:405px;width:473px;font-size:7.5px;line-height:10.4px;color:#444}
.welcome-p .lead{color:var(--orange);font-size:11px}
.btn{color:var(--white);font-size:9.5px;text-align:center;display:flex;align-items:center;justify-content:center}
.btn-orange{background:var(--orange)}
.btn-green{background:var(--green)}

.products{left:0;top:502px;width:811px;height:250px;background:linear-gradient(180deg,#8a8f82 0%,#7c8a5a 45%,#6f8a3a 100%)}
.products-h{left:0;top:520px;width:811px;text-align:center;color:var(--white);font-size:22px;font-weight:600}
.prod{top:574px;width:200px;height:131px}
.small-arrow{width:18px;height:18px;background:var(--orange)}

.band{left:0;top:752px;width:811px;height:163px;background:var(--grey-band)}
.card{top:770px;width:140px;height:119px;background:var(--white)}
.card .icon{left:10px;top:11px;width:24px;height:24px;border-radius:50%}
.card h3{left:42px;top:9px;font-size:13.5px;font-weight:300;line-height:17px;white-space:nowrap}
.card p{left:10px;top:51px;width:120px;font-size:7.3px;line-height:10.4px;text-align:center;color:#666}
.card .btn{top:108px;left:30px;width:75px;height:22px}

.partners{left:0;top:915px;width:811px;height:81px;background:var(--white)}
.partner{top:942px;display:flex;align-items:center;gap:8px;font-weight:700;color:#333}

.footer{left:0;top:996px;width:811px;height:161px;background:var(--dark)}
.fcol{top:1012px;color:var(--white)}
.fcol h4{font-size:12px;font-weight:400;white-space:nowrap}
.fcol p{font-size:7.5px;line-height:13.8px}
.fcol .txt{font-size:7.8px;line-height:10.4px;margin-top:12px}
.socials{display:flex;gap:9px;margin-top:10px}
.socials i{display:block;width:15px;height:15px}
.email{left:550px;top:1090px;width:113px;height:21px;background:var(--white);color:#444;font-size:7.5px;padding:6px 8px}
.subscribe{left:663px;top:1090px;width:53px;height:21px;background:var(--orange);font-size:8.5px}
.fnav{left:0;top:1132px;width:811px;display:flex;justify-content:center;gap:19px;font-size:10px;color:var(--white)}
.copyright{left:0;top:1157px;width:811px;height:43px;background:var(--orange);color:var(--white);font-size:7px;text-align:center;padding-top:17px}
</style>
</head>
<body>

<div class="abs topbar">
  <nav class="abs links"><a>Vector</a><a>KW Grain</a><a>Trademarks</a><a>Links</a><a>Site Map</a><a>Trait Stewardship</a></nav>
  <div class="abs call">Can we help ? Call Toll-free! <b>1-800 555-0142</b></div>
  <div class="abs agent" role="img" aria-label="Support agent portrait"></div>
</div>

<header class="abs header"></header>
<div class="abs brand"><i class="dot"></i><span>KW GRAIN</span></div>
<div class="abs search">
  <svg width="26" height="24" viewBox="0 0 26 24"><circle cx="12" cy="11" r="4" fill="none" stroke="#fff" stroke-width="1.8"/><line x1="15" y1="14" x2="18" y2="17" stroke="#fff" stroke-width="2"/></svg>
</div>
<nav class="abs nav">
  <a class="active">Home</a><a>Our Story</a><a>KW Grain Today</a><a>Walter's Legacy</a><a>Friends</a><a>Products</a><a>Events &amp; Getaways</a><a>Contact</a>
</nav>

<section class="abs hero" role="img" aria-label="Close-up photo of a ripening corn ear among green leaves"></section>
<div class="abs arrow" style="left:66px;top:194px"><svg width="29" height="28"><path d="M17 8l-6 6 6 6" fill="none" stroke="#fff" stroke-width="2.2"/></svg></div>
<div class="abs arrow" style="left:714px;top:194px"><svg width="29" height="28"><path d="M12 8l6 6-6 6" fill="none" stroke="#fff" stroke-width="2.2"/></svg></div>
<div class="abs quote">“Neque porro quisquam est, qui dolorem ipsum quia dolor sit amet,<br>consectetur, adipisci velit, sed quia non numquam eius modi.”</div>

<div class="abs video" role="img" aria-label="Video thumbnail of a farm field at sunset"></div>
<svg class="abs" style="left:138px;top:409px" width="42" height="42"><circle cx="21" cy="21" r="20" fill="rgba(80,80,80,.6)"/><path d="M16 12l13 9-13 9z" fill="#fff"/></svg>
<h1 class="abs welcome-h">Wecome to <em>KW</em> GRAIN</h1>
<p class="abs welcome-p">How are you today? Welcome too <span class="lead">KW GRAIN.</span> Neque porro quisquam est, qui dolorem ipsum quia dolor sit amet, consectetur, adipisci velit, sed quia non numquam eius modi tempora incidunt ut labore et dolore magnam aliquam quaerat voluptatem. Ut enim ad i velitm eius modi tempora incidunt ut labore et dolore magnam aliquam quaerat voluptatem. voluptatem. Ut enim ad minima veniam, quis nostrum exercitationem ullam corporis suscipit laboriosam,</p>
<a class="abs btn btn-orange" style="left:266px;top:460px;width:74px;height:22px">Read More</a>

<section class="abs products" role="img" aria-label="Blurred background photo of soybean plants"></section>
<h2 class="abs products-h">Products</h2>
<div class="abs prod" style="left:90px;background:linear-gradient(135deg,#8a5a2e,#d9b27a 55%,#7a4a22)" role="img" aria-label="Soybeans spilling from a burlap sack"></div>
<div class="abs prod" style="left:306px;background:linear-gradient(135deg,#3a3f44,#c99a3a 50%,#e8b33a 70%,#2e3438)" role="img" aria-label="Dried corn kernels in a bowl beside corn cobs"></div>
<div class="abs prod" style="left:521px;background:linear-gradient(135deg,#8a4a30,#e0c48a 50%,#9a5a3a)" role="img" aria-label="Bowl of soybeans on a wooden mat"></div>
<div class="abs small-arrow" style="left:66px;top:618px"><svg width="18" height="18"><path d="M11 5l-4 4 4 4" fill="none" stroke="#fff" stroke-width="1.8"/></svg></div>
<div class="abs small-arrow" style="left:726px;top:623px"><svg width="18" height="18"><path d="M7 5l4 4-4 4" fill="none" stroke="#fff" stroke-width="1.8"/></svg></div>

<section class="abs band"></section>
<article class="abs card" style="left:88px">
  <i class="abs icon" style="background:var(--orange)"></i>
  <h3 class="abs" style="color:var(--orange)">A Friend<br>On Your Farm</h3>
  <p class="abs">Contrary to popular belief, Lorem Ipsum is not simply random text. It has roots in a piece of classical Latin years old. Adam Bertrand.</p>
  <a class="abs btn btn-orange">Read More</a>
</article>
<article class="abs card" style="left:251px">
  <i class="abs icon" style="background:var(--green)"></i>
  <h3 class="abs" style="color:var(--green)">The Seed<br>You Need</h3>
  <p class="abs">Contrary to popular belief, Lorem Ipsum is not simply random text. It has roots in a piece of classical Latin years old. Adam Bertrand.</p>
  <a class="abs btn btn-green">Read More</a>
</article>
<article class="abs card" style="left:414px">
  <i class="abs icon" style="background:var(--green)"></i>
  <h3 class="abs" style="color:var(--green)">Connecting<br>People</h3>
  <p class="abs">Contrary to popular belief, Lorem Ipsum is not simply random text. It has roots in a piece of classical Latin years old. Adam Bertrand.</p>
  <a class="abs btn btn-green">Read More</a>
</article>
<article class="abs card" style="left:577px">
  <i class="abs icon" style="background:var(--green)"></i>
  <h3 class="abs" style="color:var(--green)">Fun<br>In The Field</h3>
  <p class="abs">Contrary to popular belief, Lorem Ipsum is not simply random text. It has roots in a piece of classical Latin years old. Adam Bertrand.</p>
  <a class="abs btn btn-green">Read More</a>
</article>

<section class="abs partners"></section>
<div class="abs partner" style="left:98px;font-size:14px"><i style="display:block;width:14px;height:14px;background:#d71f26"></i>Norrow CropSciences</div>
<div class="abs partner" style="left:395px;font-size:16px;color:#1f8a44">Fieldmark</div>
<div class="abs partner" style="left:570px;font-size:18px;color:#222">Molvan</div>

<footer class="abs footer"></footer>
<div class="abs fcol" style="left:66px;width:230px">
  <h4>Contact us for the Quality You Deserve!</h4>
  <div style="margin-top:9px">
    <p>P.O. Box 218, Alder Creek, FL 34001</p>
    <p>Phone: (941) 555-0187</p>
    <p>Fax: (941) 555-0193</p>
    <p>Email: contact@kwgrain.com</p>
    <p>Web: <span style="color:var(--orange)">www.kwgrain.com</span></p>
  </div>
</div>
<div class="abs fcol" style="left:318px;width:172px">
  <h4>Get Social with us!</h4>
  <p class="txt">This is just a place holder, so you can see what the site would look like. This is just a place holder, so you can see what the site would look like..</p>
  <div class="socials">
    <i style="background:#4a68a8"></i><i style="background:#c8232c"></i><i style="background:#2ea3d6"></i><i style="background:#c4432f"></i><i style="background:#1a78b4"></i><i style="background:#d42a24"></i>
  </div>
</div>
<div class="abs fcol" style="left:545px;width:172px">
  <h4>News Letter</h4>
  <p class="txt">Numquam eius modi tempora incidunt ut labore et dolore magnam aliquam qua era t vol up tatem. Ut enim ad minima veniam, quis nostr um exercitationem ullam corporis suscipit .</p>
</div>
<div class="abs email">Email</div>
<a class="abs btn subscribe">Subscribe</a>
<nav class="abs fnav"><a>Home</a><a>Our Story</a><a>KW Grain Today</a><a>Walter's Legacy</a><a>Friends</a><a>Products</a><a>Events &amp; Getaways</a><a>Contact</a></nav>
<div class="abs copyright">Copyright© 2015. All Rights Reserved.</div>

</body>
</html>
```